Business cards to launch an education platform

Hi,
I am looking at having new business cards designed.
I am a startup, developing a web platform for schools and university, the education world. It's an online assessment system.
I would like a card that looks classy, and that is using the colors and the font of my logo.

I have attached:
1) my logo
2) A business card that I have designed quickly so you can have all the information required in the card, but I really don't like it.
3) The font that I am using (Lato Regular) to design my web platform
4) Some screenshots of my web platform so you can have a look at the style that I have.

Target Market(s)

Major market: Education system: Schools and university
Minor markets: Business in general

Industry/Entity Type

Business

Contact Information for Business Card

Clara Fenwick
Director

M: 0437 518 902
E: clara.fenwick@amberLoomSystems.com.au

Requirements
Must have
• The colors of my logo

```html
<!DOCTYPE html>
<html lang="en">
<head>
<meta charset="utf-8">
<title>Amber Loom Systems – Business Cards</title>
<link rel="stylesheet" href="https://fonts.googleapis.com/css2?family=Lato:wght@400;700&family=PT+Sans+Narrow:wght@400;700&display=swap">
<style>
  :root {
    --page-bg: #e9ebee;
    --navy-deep: #0b3d6e;
    --navy: #0f4f8a;
    --navy-light: #1a63a3;
    --sky: #5cc8ef;
    --sky-soft: #9ad9f3;
    --white: #ffffff;
    --rule: rgba(255, 255, 255, 0.55);
    --brand-blue: #1b6fb8;
    --card-shadow: 0 18px 40px rgba(10, 30, 60, 0.18);
  }
  * { box-sizing: border-box; margin: 0; padding: 0; }
  html, body {
    width: 1200px;
    height: 950px;
    overflow: hidden;
    background: var(--page-bg);
  }
  .sheet {
    width: 1200px;
    height: 950px;
    display: flex;
    flex-direction: column;
    align-items: center;
    justify-content: center;
    gap: 60px;
  }
  .card {
    position: relative;
    width: 700px;
    height: 400px;
    border-radius: 4px;
    box-shadow: var(--card-shadow);
    overflow: hidden;
  }

  /* Contact side */
  .card--contact {
    background: linear-gradient(135deg, var(--navy-light) 0%, var(--navy) 45%, var(--navy-deep) 100%);
    color: var(--white);
  }
  .contact {
    position: absolute;
    left: 56px;
    bottom: 58px;
    width: 520px;
  }
  .contact__name {
    font-family: "PT Sans Narrow", sans-serif;
    font-weight: 400;
    font-size: 34px;
    letter-spacing: 1px;
    text-transform: uppercase;
    color: var(--sky);
    line-height: 1;
  }
  .contact__role-row {
    display: flex;
    align-items: center;
    gap: 14px;
    margin-top: 6px;
  }
  .contact__role {
    font-family: "PT Sans Narrow", sans-serif;
    font-weight: 700;
    font-size: 22px;
    letter-spacing: 0.5px;
    text-transform: uppercase;
  }
  .contact__rule {
    flex: 1;
    height: 1px;
    background: var(--rule);
  }
  .contact__line {
    font-family: "Lato", sans-serif;
    font-size: 17px;
    margin-top: 10px;
    color: var(--white);
  }
  .contact__label { color: var(--sky); }
  .contact__email { margin-top: 6px; }

  .divider {
    position: absolute;
    left: 340px;
    right: 60px;
    top: 190px;
    height: 1px;
    background: var(--rule);
  }
  .brand-corner {
    position: absolute;
    right: 60px;
    top: 62px;
    display: flex;
    align-items: center;
    gap: 12px;
  }
  .brand-corner__square {
    width: 54px;
    height: 54px;
    background: var(--sky);
  }
  .brand-corner__name {
    font-family: "Lato", sans-serif;
    font-weight: 400;
    font-size: 20px;
    color: var(--sky);
  }

  /* Brand side */
  .card--brand {
    background: var(--white);
    display: flex;
    align-items: center;
    justify-content: center;
  }
  .brand {
    display: flex;
    align-items: center;
    gap: 22px;
  }
  .brand__square {
    width: 90px;
    height: 90px;
    background: var(--brand-blue);
  }
  .brand__name {
    font-family: "Lato", sans-serif;
    font-weight: 400;
    font-size: 44px;
    letter-spacing: 1px;
    color: var(--brand-blue);
  }
</style>
</head>
<body>
<main class="sheet">
  <section class="card card--contact" aria-label="Business card, contact side">
    <div class="brand-corner">
      <span class="brand-corner__square" aria-hidden="true"></span>
      <span class="brand-corner__name">Amber Loom Systems</span>
    </div>
    <div class="divider" aria-hidden="true"></div>
    <div class="contact">
      <p class="contact__name">Clara Fenwick</p>
      <div class="contact__role-row">
        <p class="contact__role">Director</p>
        <span class="contact__rule" aria-hidden="true"></span>
      </div>
      <p class="contact__line"><span class="contact__label">Mobile :</span> 0437 518 902</p>
      <p class="contact__line contact__email">clara.fenwick@amberLoomSystems.com.au</p>
    </div>
  </section>

  <section class="card card--brand" aria-label="Business card, brand side">
    <div class="brand">
      <span class="brand__square" aria-hidden="true"></span>
      <span class="brand__name">Amber Loom Systems</span>
    </div>
  </section>
</main>
</body>
</html>
```